DeskHarbor - Coworking website design

DeskHarbor is a new global coworking brand, growing fast and establishing stylish locations and communities that inspire innovation and collaboration all around the world.
The project includes a complete website design, focused on delivering the company’s values and messages, provide information to site visitors and to generate leads.

Please review the attached design brief, for more information.

Target Market(s)

Both men and women. Decision makers in:
Small & medium businesses in various fields, but mainly technology firms (Startups or established brands).
Global enterprises.
Dynamic “new generation” companies.
Press

Number of Pages Required

2 page

Requirements
Must have
• Project Scope & deliverables:
• Concept and design for :
• Home page
• Deliver the values mentioned above.
• Showcase the cities in which the company has locations in.
• Show customer testimonials.
• Provide an interface (form) for booking a tour and/or leaving contact details for more information (two alternatives)
• Coworking location page - Each location is in the coolest part of a different major city, and has its own address, set of amenities (kitchen, fast internet etc,), area information (public transportation accessibility, sites near by, bars and restaurants in walking distance) and pricing for private offices (based on number of people per office). Each location page must have an interface to book a location tour.
• Site Navigation (header & footer) - allow simple navigation between multiple city pages, location pages and homepage. Growth of up to 50 locations in 25 cities.
• The navigation should account for Navigation to additional pages (not commissioned in this project) such as:
• Locations
• Enterprise
• Special promotions
• Blog
• Contact us
• About us
• Note - the site should account for geolocation variable display, showing different content for different locations.
• Deliverables must include all editable graphic files (photoshop or similar), as follows:
• Home page - Desktop view (preferably both)
• Location page - Mobile web view (preferably both)
• Navigation - both options

```html
<!DOCTYPE html>
<html lang="en">
<head>
<meta charset="utf-8">
<title>DeskHarbor – Coworking</title>
<link href="https://fonts.googleapis.com/css2?family=Lato:wght@300;400;700;900&display=swap" rel="stylesheet">
<style>
:root{
  --orange:#ff8a00;
  --orange-deep:#f57c00;
  --ink:#1f1f1f;
  --text:#4a4a4a;
  --muted:#7a7a7a;
  --light:#f0f0f0;
  --panel-dark:#222;
  --panel-light:#ececec;
  --band-gray:#8c8c8c;
  --line:#d6d6d6;
  --white:#fff;
}
*{box-sizing:border-box;margin:0;padding:0}
html,body{width:1200px;height:4523px;overflow:hidden;background:var(--white)}
body{font-family:'Lato',sans-serif;color:var(--text);position:relative}
.abs{position:absolute}

/* header */
.site-header{position:absolute;left:0;top:0;width:1200px;height:95px;background:var(--white)}
.brand{position:absolute;left:120px;top:30px;font-size:29px;font-weight:700;color:var(--ink)}
.main-nav{position:absolute;left:435px;top:40px;display:flex;gap:30px;font-size:15px;color:var(--text)}

/* hero */
.hero{position:absolute;left:0;top:95px;width:1200px;height:530px;background:var(--light);overflow:hidden}
.hero-photo{position:absolute;inset:0;background:linear-gradient(135deg,#cfd6dc 0%,#8d97a0 40%,#3b3f44 100%);clip-path:polygon(660px 0,1160px 0,1160px 530px,340px 530px)}
.hero-photo::after{content:"";position:absolute;right:0;top:0;width:40px;height:530px;background:#fff}
.hero h1{position:absolute;left:114px;top:116px;width:380px;font-size:35px;line-height:40px;font-weight:700;color:var(--ink)}
.hero p{position:absolute;left:114px;top:250px;width:330px;font-size:14px;line-height:19px;color:var(--text)}
.btn-orange{position:absolute;background:var(--orange);color:#fff;font-size:16px;text-align:center;border:none}
.hero .btn-orange{left:114px;top:318px;width:166px;height:36px;line-height:36px}
.slider-dots{position:absolute;left:114px;top:380px;display:flex;gap:10px}
.slider-dots span{width:34px;height:4px;background:#bdbdbd}
.slider-dots span.active{background:var(--orange)}

/* welcome */
.welcome-photo{position:absolute;left:155px;top:665px;width:340px;height:340px;border-radius:50%;border:2px solid #cfcfcf;padding:8px}
.welcome-photo div{width:100%;height:100%;border-radius:50%;background:radial-gradient(circle at 40% 40%,#e6e6e6,#9aa0a6 70%,#5c6166)}
.welcome h2{position:absolute;left:527px;top:702px;font-size:34px;font-weight:700;color:var(--ink)}
.welcome p{position:absolute;left:532px;top:765px;width:520px;font-size:13.5px;line-height:22px}
.btn-outline{position:absolute;left:537px;top:925px;width:168px;height:42px;border:2px solid #9a9a9a;text-align:center;line-height:38px;font-size:15px;color:var(--text)}

/* values */
.values{position:absolute;left:0;top:1045px;width:1200px;height:360px;background:var(--orange)}
.values h2{position:absolute;left:0;width:1200px;top:40px;text-align:center;color:#fff;font-size:30px;font-weight:700}
.value{position:absolute;top:128px;width:200px;text-align:center;color:#fff;font-size:17px;font-weight:700;line-height:21px}
.value svg{display:block;margin:0 auto 14px;width:92px;height:92px}

/* experience */
.section-title{position:absolute;left:0;width:1200px;text-align:center;font-size:29px;font-weight:700;color:var(--ink)}
.section-title.ruled span{padding:0 18px;position:relative}
.section-title.ruled span::before,.section-title.ruled span::after{content:"";position:absolute;top:50%;width:34px;height:2px;background:#777}
.section-title.ruled span::before{right:100%}
.section-title.ruled span::after{left:100%}
.space-photo{position:absolute;width:495px;height:325px}
.space-card{position:absolute;width:495px;height:325px;padding:40px 48px}
.space-card h3{font-size:24px;font-weight:400;margin-bottom:8px}
.space-card .lead{font-size:13px;line-height:18px;margin-bottom:14px}
.space-card ul{list-style:none;font-size:14px;line-height:31px}
.space-card li::before{content:"› ";font-weight:700}
.space-card.dark{background:var(--panel-dark);color:#e6e6e6}
.space-card.dark h3{color:#fff}
.space-card.plain{background:#fff;color:var(--text)}
.space-card.plain h3,.space-card.light h3{color:var(--ink)}
.space-card.light{background:var(--panel-light);color:var(--text)}

/* testimonials */
.testimonials{position:absolute;left:0;top:2590px;width:1200px;height:440px;background:var(--band-gray)}
.testimonials h2{position:absolute;left:0;width:1200px;top:45px;text-align:center;color:#fff;font-size:29px;font-weight:400}
.arrow{position:absolute;top:228px;width:26px;height:40px}
.quote{position:absolute;text-align:center;padding:0 18px}
.quote .avatar{border-radius:50%;background:linear-gradient(#c9b8a6,#6f5d50);margin:0 auto}
.quote .name{font-weight:700;text-transform:uppercase;color:var(--ink)}
.quote.side{top:140px;width:242px;height:205px;background:#6f6f6f;color:#ededed;font-size:10.5px;line-height:15px;padding-top:18px}
.quote.side .avatar{width:56px;height:56px;margin-bottom:10px}
.quote.side .name{color:#fff;font-size:10.5px;margin-bottom:6px}
.quote.main{top:118px;left:457px;width:278px;height:242px;background:#fff;color:var(--text);font-size:12.5px;line-height:17px;padding-top:22px;box-shadow:0 2px 10px rgba(0,0,0,.25)}
.quote.main .avatar{width:66px;height:66px;margin-bottom:10px}
.quote.main .name{font-size:12.5px;margin-bottom:8px}

/* locations */
.map{position:absolute;left:110px;top:3140px;width:950px;height:450px;background:radial-gradient(ellipse at 50% 45%,#d2d2d2 0%,#dedede 55%,#fff 80%)}
.pin{position:absolute;width:22px;height:30px}

/* contact */
.contact{position:absolute;left:0;top:3635px;width:1200px;height:510px;background:linear-gradient(120deg,#d9d9d9,#ececec 45%,#dcdcdc)}
.contact h2{position:absolute;left:0;width:1200px;top:48px;text-align:center;font-size:29px;font-weight:400;color:var(--ink)}
.contact-form{position:absolute;left:395px;top:115px;width:415px;height:345px;background:#fff;box-shadow:0 2px 12px rgba(0,0,0,.12)}
.field{position:absolute;left:35px;width:348px;height:38px;border:1px solid #cfcfcf;font-size:13px;color:#9a9a9a;padding-left:16px;line-height:36px}
.contact-form .btn-orange{left:35px;top:260px;width:348px;height:44px;line-height:44px;font-size:17px}

/* footer */
.footer-col h4{position:absolute;top:4205px;font-size:16px;font-weight:700;color:var(--ink);letter-spacing:.5px}
.footer-links{position:absolute;top:4250px;list-style:none;font-size:13.5px;line-height:31px;color:var(--text)}
.signup-input{position:absolute;left:600px;top:4248px;width:255px;height:42px;border:1px solid #cfcfcf;font-size:13px;color:#9a9a9a;padding-left:14px;line-height:40px}
.signup-btn{position:absolute;left:855px;top:4248px;width:150px;height:42px;background:var(--panel-dark);color:#fff;font-size:16px;font-weight:700;text-align:center;line-height:42px}
.social{position:absolute;left:600px;top:4320px;display:flex;gap:24px}
.social span{width:18px;height:18px;border-radius:50%;background:var(--ink)}
.footer-rule{position:absolute;left:118px;top:4455px;width:964px;height:1px;background:var(--line)}
.copyright{position:absolute;left:0;width:1200px;top:4473px;text-align:center;font-size:13px;color:var(--muted)}
</style>
</head>
<body>

<header class="site-header">
  <div class="brand">DeskHarbor</div>
  <nav class="main-nav">
    <span>Locations</span><span>Enterprise</span><span>Special promotions</span><span>Blog</span><span>Contact us</span><span>About us</span>
  </nav>
</header>

<section class="hero">
  <div class="hero-photo" role="img" aria-label="Photo of a team meeting around a table in a bright office with large windows"></div>
  <h1>Inspire Innovation and Collaboration all around the world.</h1>
  <p>Morbi diam mauris viverra in gravida eu mattis in ante Morbi eget arcu Morbi porta liber</p>
  <div class="btn-orange">Contact Us</div>
  <div class="slider-dots"><span></span><span></span><span class="active"></span><span></span></div>
</section>

<section class="welcome">
  <div class="welcome-photo"><div role="img" aria-label="Photo of people working on laptops at a shared desk"></div></div>
  <h2>Welcome to DeskHarbor</h2>
  <p>Coworking is a style of work that involves a shared working environment. Unlike in a typical office environment, those coworking are usually employed by various organizations. Coworking is a gathering of a group of people who are working independently, but who share values, and who are interested in the synergy that can happen from working with like-minded people.</p>
  <div class="btn-outline">Learn More</div>
</section>

<section class="values">
  <h2>Our Values</h2>
  <div class="value" style="left:125px">
    <svg viewBox="0 0 92 92" fill="none" stroke="#fff" stroke-width="2.5"><circle cx="46" cy="46" r="40" stroke-dasharray="4 5"/><circle cx="46" cy="46" r="26"/><path d="M46 30v10M38 50h16M40 58h12"/><circle cx="46" cy="45" r="6"/></svg>
    Inspire collaboration<br>&amp; Innovation
  </div>
  <div class="value" style="left:315px">
    <svg viewBox="0 0 92 92" fill="none" stroke="#fff" stroke-width="2.5"><circle cx="34" cy="56" r="14"/><circle cx="34" cy="56" r="5"/><circle cx="60" cy="32" r="11"/><circle cx="60" cy="32" r="4"/><path d="M20 30c4-10 14-16 24-16M70 60c-3 10-12 16-22 18"/></svg>
    Idea sharing
  </div>
  <div class="value" style="left:500px">
    <svg viewBox="0 0 92 92" fill="none" stroke="#fff" stroke-width="3"><path d="M10 40 46 12l36 28"/><path d="M18 36v44h56V36"/><circle cx="34" cy="52" r="7"/><circle cx="58" cy="52" r="7"/><path d="M22 78c0-10 6-16 12-16s12 6 12 16M46 78c0-10 6-16 12-16s12 6 12 16"/></svg>
    Be a part of an<br>Exclusive Club
  </div>
  <div class="value" style="left:693px">
    <svg viewBox="0 0 92 92" fill="none" stroke="#fff" stroke-width="2.5"><path d="M14 34l14 14 18-26 18 26 14-14-6 34H20z"/><path d="M20 76h52"/><circle cx="14" cy="32" r="3"/><circle cx="46" cy="20" r="3"/><circle cx="78" cy="32" r="3"/></svg>
    Realize Your<br>Greatness
  </div>
  <div class="value" style="left:875px">
    <svg viewBox="0 0 92 92" fill="none" stroke="#fff" stroke-width="2.5"><path d="M46 18a20 20 0 0 0-12 36v10h24V54a20 20 0 0 0-12-36z"/><path d="M36 72h20M40 80h12M46 6v6M18 20l5 5M74 20l-5 5M10 44h6M76 44h6"/></svg>
    Style and Design<br>Awareness
  </div>
</section>

<h2 class="section-title ruled" style="top:1472px"><span>Experience Our Working Space</span></h2>

<div class="space-photo" style="left:120px;top:1545px;background:linear-gradient(135deg,#c8cfc4,#7a8a70 50%,#4b4e45)" role="img" aria-label="Photo of an open coworking floor with green chairs and large windows"></div>
<div class="space-card dark" style="left:615px;top:1545px">
  <h3>Working Space Title</h3>
  <p class="lead">Etiam eu urna Sed porta Suspendisse quam leo molestie sed luctus quis feugiat in pede Fusce tellus Sed metus</p>
  <ul><li>Etiam eu urna Sed porta Suspendisse</li><li>Auam leo molestie sed</li><li>Luctus quis feugiat in pede</li><li>Fusce tellus Sed metus</li></ul>
</div>

<div class="space-card plain" style="left:120px;top:1870px">
  <h3>Working Space Title</h3>
  <p class="lead">Etiam eu urna Sed porta Suspendisse quam leo molestie sed luctus quis feugiat in pede Fusce tellus Sed metus</p>
  <ul><li>Etiam eu urna Sed porta Suspendisse</li><li>Auam leo molestie sed</li><li>Luctus quis feugiat in pede</li><li>Fusce tellus Sed metus</li></ul>
</div>
<div class="space-photo" style="left:612px;top:1870px;background:linear-gradient(135deg,#d8d8d8,#9c8f86 50%,#d2692a 80%,#5a5a5a)" role="img" aria-label="Photo of rows of desks with orange chairs in an office"></div>

<div class="space-photo" style="left:120px;top:2193px;background:linear-gradient(135deg,#f2f2f2,#c4c4c4 55%,#6a6a6a)" role="img" aria-label="Photo of a bright white meeting room with black chairs"></div>
<div class="space-card light" style="left:615px;top:2193px">
  <h3>Working Space Title</h3>
  <p class="lead">Etiam eu urna Sed porta Suspendisse quam leo molestie sed luctus quis feugiat in pede Fusce tellus Sed metus</p>
  <ul><li>Etiam eu urna Sed porta Suspendisse</li><li>Auam leo molestie sed</li><li>Luctus quis feugiat in pede</li><li>Fusce tellus Sed metus</li></ul>
</div>

<section class="testimonials">
  <h2>Client Testimonial</h2>
  <svg class="arrow" style="left:106px" viewBox="0 0 26 40" fill="none" stroke="#fff" stroke-width="4"><path d="M22 4 6 20l16 16"/></svg>
  <svg class="arrow" style="left:1048px" viewBox="0 0 26 40" fill="none" stroke="#fff" stroke-width="4"><path d="M4 4l16 16L4 36"/></svg>
  <div class="quote side" style="left:182px">
    <div class="avatar" role="img" aria-label="Client portrait"></div>
    <div class="name">Reza Holloway</div>
    Etiam eu urna Sed porta Suspendisse quam leo molestie sed luctus quis feugiat in pede Fusce tellus Sed metus augue convallis
  </div>
  <div class="quote main">
    <div class="avatar" role="img" aria-label="Client portrait"></div>
    <div class="name">Milo Brandt</div>
    Etiam eu urna Sed porta Suspendisse quam leo molestie sed luctus quis feugiat in pede Fusce tellus Sed metus augue convallis
  </div>
  <div class="quote side" style="left:762px">
    <div class="avatar" role="img" aria-label="Client portrait"></div>
    <div class="name">Ines Carrow</div>
    Etiam eu urna Sed porta Suspendisse quam leo molestie sed luctus quis feugiat in pede Fusce tellus Sed metus augue convallis
  </div>
</section>

<h2 class="section-title" style="top:3078px;font-weight:400">Location Cities</h2>
<div class="map" role="img" aria-label="Gray world map showing the cities with coworking locations"></div>
<svg class="pin" style="left:298px;top:3180px" viewBox="0 0 22 30"><path d="M11 0a11 11 0 0 0-11 11c0 8 11 19 11 19s11-11 11-19A11 11 0 0 0 11 0z" fill="#111"/><circle cx="11" cy="11" r="4" fill="#fff"/></svg>
<svg class="pin" style="left:538px;top:3215px" viewBox="0 0 22 30"><path d="M11 0a11 11 0 0 0-11 11c0 8 11 19 11 19s11-11 11-19A11 11 0 0 0 11 0z" fill="#111"/><circle cx="11" cy="11" r="4" fill="#fff"/></svg>
<svg class="pin" style="left:875px;top:3255px" viewBox="0 0 22 30"><path d="M11 0a11 11 0 0 0-11 11c0 8 11 19 11 19s11-11 11-19A11 11 0 0 0 11 0z" fill="#111"/><circle cx="11" cy="11" r="4" fill="#fff"/></svg>
<svg class="pin" style="left:660px;top:3335px" viewBox="0 0 22 30"><path d="M11 0a11 11 0 0 0-11 11c0 8 11 19 11 19s11-11 11-19A11 11 0 0 0 11 0z" fill="#111"/><circle cx="11" cy="11" r="4" fill="#fff"/></svg>
<svg class="pin" style="left:565px;top:3375px" viewBox="0 0 22 30"><path d="M11 0a11 11 0 0 0-11 11c0 8 11 19 11 19s11-11 11-19A11 11 0 0 0 11 0z" fill="#111"/><circle cx="11" cy="11" r="4" fill="#fff"/></svg>
<svg class="pin" style="left:343px;top:3385px" viewBox="0 0 22 30"><path d="M11 0a11 11 0 0 0-11 11c0 8 11 19 11 19s11-11 11-19A11 11 0 0 0 11 0z" fill="#111"/><circle cx="11" cy="11" r="4" fill="#fff"/></svg>
<svg class="pin" style="left:890px;top:3460px" viewBox="0 0 22 30"><path d="M11 0a11 11 0 0 0-11 11c0 8 11 19 11 19s11-11 11-19A11 11 0 0 0 11 0z" fill="#111"/><circle cx="11" cy="11" r="4" fill="#fff"/></svg>

<section class="contact" role="img" aria-label="Faded photo of a desk with a keyboard, glasses, notebook and coffee cup">
  <h2>Want to Contact Us</h2>
  <form class="contact-form">
    <div class="field" style="top:38px">First Name</div>
    <div class="field" style="top:91px">Last Name</div>
    <div class="field" style="top:145px">Email address</div>
    <div class="field" style="top:198px">Phone</div>
    <div class="btn-orange">Request Invitation</div>
  </form>
</section>

<footer>
  <div class="footer-col"><h4 style="left:135px">QUICK LINKS</h4></div>
  <ul class="footer-links" style="left:135px"><li>Locations</li><li>Enterprise</li><li>Special promotions</li><li>Blog</li></ul>
  <div class="footer-col"><h4 style="left:382px">RESOURCES</h4></div>
  <ul class="footer-links" style="left:382px"><li>About us</li><li>Why Us</li><li>Contact us</li><li>Terms of Use</li></ul>
  <div class="footer-col"><h4 style="left:600px">EMAIL SIGN UP</h4></div>
  <div class="signup-input">Email address</div>
  <div class="signup-btn">Subscribe</div>
  <div class="social" aria-label="Social links"><span></span><span></span><span></span><span></span><span></span></div>
  <div class="footer-rule"></div>
  <div class="copyright">© 2017 Company Name. All right reserved</div>
</footer>

</body>
</html>
```